Website Design for Wheels for Servicemen.org - Donated Cars to Disabled Vets

Need a Wordpress website. The coding now, esp. the CDONT coding is not supported by many hosting sites. Looking for a landing page to generate leads.

Logo Text

look at current one for ideas

Coding

Coded - Design and coding required

Number of Pages Required

1 page

Requirements
Must have
• look at current website at www.wheelsforservicemen.org
Nice to have
• look at this site: http://givevehicletoservicemen.org

```html
<!DOCTYPE html>
<html lang="en">
<head>
<meta charset="utf-8">
<title>Wheels for Servicemen – Donate Your Car</title>
<link rel="stylesheet" href="https://fonts.googleapis.com/css2?family=Noto+Serif:wght@400;700&family=Open+Sans:wght@400;600;700&family=Oswald:wght@500&display=swap">
<style>
:root{
  --blue:#1d5fb4;
  --blue-dark:#134a92;
  --nav:#164f9c;
  --red:#c8202f;
  --red-dark:#a9141f;
  --ink:#333;
  --muted:#666;
  --page:#ededed;
  --white:#fff;
  --line:#e1e1e1;
}
*{box-sizing:border-box;margin:0;padding:0}
html,body{width:1200px;height:3010px;overflow:hidden}
body{background:var(--page);font-family:"Open Sans",Arial,sans-serif;color:var(--ink);position:relative}
.site{position:absolute;left:68px;top:36px;width:1048px;height:2974px;background:var(--white)}
.abs{position:absolute}

/* header */
.masthead{left:0;top:0;width:1048px;height:124px;background:linear-gradient(180deg,#2468bf,#1b58a8)}
.brand{left:56px;top:38px;display:flex;align-items:center;gap:12px;color:var(--white);font-size:22px;font-weight:700}
.brand-mark{width:26px;height:26px;background:var(--red);border-radius:4px}
.tagline{left:400px;top:36px;color:var(--white);font-family:"Noto Serif",serif;font-size:19px;font-weight:700;line-height:26px}
.nav{left:0;top:124px;width:1048px;height:46px;background:var(--nav);display:flex;padding-left:44px}
.nav a{color:var(--white);text-decoration:none;font-size:13px;line-height:46px;padding:0 18px;font-family:"Noto Serif",serif}
.nav a.active{border-bottom:3px solid var(--white)}

/* hero */
.hero{left:0;top:170px;width:1048px;height:372px;background:linear-gradient(100deg,#6d7258 0%,#a9a596 35%,#d7d3cc 60%,#c6c2ba 100%)}
.hero-title{left:350px;top:250px;width:260px;font-family:"Oswald",sans-serif;font-size:30px;line-height:36px;color:var(--white);text-shadow:0 1px 3px rgba(0,0,0,.35)}
.dots{left:496px;top:530px;display:flex;gap:5px}
.dots span{width:12px;height:12px;border-radius:50%;background:var(--white);border:1px solid #bbb}
.dots span:first-child{background:#ddd}

/* donate panel */
.donate-panel{left:694px;top:0;width:306px;height:542px;background:var(--red)}
.panel-head{width:306px;height:150px;background:var(--red-dark);clip-path:polygon(0 0,100% 0,100% 80%,50% 100%,0 80%);text-align:center;color:var(--white);padding-top:26px}
.panel-head p{font-family:"Noto Serif",serif;font-size:16px}
.panel-head .phone{font-size:30px;font-weight:700;margin-top:6px}
.panel-note{width:306px;text-align:center;color:var(--white);font-size:12.5px;line-height:18px;margin-top:8px}
.form{padding:14px 22px 0;display:grid;grid-template-columns:1fr 1fr;gap:12px 10px}
.field{height:32px;background:var(--white);border-radius:2px;font-size:10.5px;color:#888;line-height:32px;padding-left:10px;position:relative}
.field.wide{grid-column:1/3}
.field.select::after{content:"";position:absolute;right:8px;top:13px;border:4px solid transparent;border-top-color:#777}
.submit{grid-column:1/3;justify-self:center;margin-top:6px;width:188px;height:36px;background:#2c2c2c;color:var(--white);font-family:"Noto Serif",serif;font-size:14px;font-weight:700;text-align:center;line-height:36px;border-radius:3px}

/* sections */
.h2{font-family:"Noto Serif",serif;font-weight:700;color:#333;text-align:center;width:1048px;left:0}
.steps-title{top:588px;font-size:29px}
.step{top:654px;width:320px;height:130px}
.step .pin{position:absolute;left:0;top:0}
.step h3{position:absolute;left:92px;top:8px;font-family:"Noto Serif",serif;font-weight:400;font-size:13.5px;color:var(--red);white-space:nowrap}
.step p{position:absolute;left:92px;top:34px;width:200px;font-size:10.5px;line-height:17px;color:var(--muted)}
.step .more{position:absolute;left:92px;top:104px;font-size:10px;color:#444;text-transform:uppercase}

.welcome-title{top:906px;font-size:31px}
.welcome-text{left:114px;top:960px;width:820px;text-align:center;font-size:10.5px;line-height:19px;color:var(--muted)}
.donate-btn{left:462px;top:1032px;width:136px;height:44px;border-radius:22px;background:var(--red);color:var(--white);font-family:"Oswald",sans-serif;font-size:15px;display:flex;align-items:center;justify-content:center;gap:8px}
.donate-btn i{width:20px;height:20px;border:2px solid var(--white);border-radius:50%;font-style:normal;font-size:11px;text-align:center;line-height:16px}

.why{left:0;top:1148px;width:524px;height:406px;background:linear-gradient(180deg,#1f64b8,#1a5aa8);color:var(--white);padding:50px 36px 0 64px}
.why h2{font-family:"Noto Serif",serif;font-size:21px;font-weight:700;margin-bottom:16px}
.why li{list-style:none;font-size:10px;line-height:16px;margin-bottom:8px;padding-left:18px;position:relative}
.why li::before{content:"";position:absolute;left:0;top:4px;width:7px;height:7px;border-radius:50%;background:var(--white)}
.why-photo{left:524px;top:1148px;width:524px;height:406px;background:linear-gradient(160deg,#d8d4da 0%,#c5c4cc 40%,#8a8c7a 75%,#b7b5ae 100%)}

.tax-title{top:1614px;font-size:29px}
.tax-sub{top:1664px;font-size:13px;font-family:"Noto Serif",serif;color:#444;text-align:center;width:1048px;left:0}
.tax-card{top:1734px;width:414px;height:196px;border:1px dashed var(--red);border-radius:6px;text-align:center;padding:36px 34px 0}
.tax-card h3{font-family:"Noto Serif",serif;font-weight:400;font-size:19px;color:var(--red)}
.tax-card h4{font-family:"Noto Serif",serif;font-weight:400;font-size:13px;color:var(--red);margin-bottom:14px}
.tax-card p{font-size:10.5px;line-height:18px;color:#555}

.today-title{top:2008px;font-size:29px}
.checks{top:2086px;font-size:11.5px;color:#444}
.checks li{list-style:none;display:flex;align-items:center;gap:12px;height:26px}
.checks svg{flex:none}

.program{left:0;top:2196px;width:1048px;height:408px;background:linear-gradient(180deg,#1b5aa9,#1f62b4 50%,#1b56a2)}
.program-title{top:56px;font-size:28px;color:var(--white)}
.prog-item{width:340px;display:flex;gap:18px}
.prog-icon{width:56px;height:52px;background:var(--red);flex:none;display:flex;align-items:center;justify-content:center;border:2px solid #e04453}
.prog-item h3{font-family:"Noto Serif",serif;font-weight:400;font-size:15px;color:var(--white);margin:2px 0 8px}
.prog-item p{font-size:10.5px;line-height:17px;color:#e6eefa}

.footer{left:0;top:2604px;width:1048px;height:260px;background:#f3f3f3}
.footer h4{font-family:"Noto Serif",serif;font-weight:400;font-size:17px;color:#333}
.input{width:228px;height:38px;background:var(--white);border:1px solid #ddd;font-size:10px;color:#888;line-height:38px;padding-left:12px}
.sub-btn{width:84px;height:28px;background:var(--blue-dark);color:var(--white);font-size:11px;font-weight:700;text-align:center;line-height:28px}
.contact li{list-style:none;font-size:11px;color:#555;line-height:18px;display:flex;gap:10px;margin-bottom:12px}
.links li{list-style:none;font-size:10.5px;color:#555;line-height:21px}
.foot-brand{font-size:15px;font-weight:700;color:#333;display:flex;gap:8px;align-items:center}
.badge{width:90px;height:40px;background:#d9d9d9;border-radius:3px}
.badge-round{width:44px;height:44px;border-radius:50%;background:#d3dbe8;border:2px solid #9fb3d1}
.bottom{left:0;top:2864px;width:1048px;height:110px;border-top:1px solid var(--line);background:#f3f3f3}
.socials{left:478px;top:18px;display:flex;gap:6px}
.socials span{width:20px;height:20px;border-radius:50%;background:var(--blue)}
.socials span:last-child{background:var(--red)}
.copy{left:0;top:52px;width:1048px;text-align:center;font-size:10.5px;color:#666}
</style>
</head>
<body>
<div class="site">

  <header class="masthead abs">
    <div class="brand abs"><span class="brand-mark"></span>Wheels for Servicemen</div>
    <p class="tagline abs">Donate your car to a vet,<br>Make a Difference</p>
  </header>
  <nav class="nav abs">
    <a class="active">Home</a><a>How It Works</a><a>Charities</a><a>Tax Deduction</a><a>FAQ</a><a>Contact</a>
  </nav>

  <section class="hero abs" role="img" aria-label="Photo of a soldier in camouflage hugging a young girl holding a small flag, parked cars behind"></section>
  <h1 class="hero-title abs">Donate Your Car to Veterans and Get a Tax Deduction</h1>
  <svg class="abs" style="left:560px;top:276px" width="150" height="110" viewBox="0 0 150 110">
    <path d="M8 100 C60 96 110 70 138 14" fill="none" stroke="#c8202f" stroke-width="4"/>
    <path d="M124 18 L140 8 L142 28" fill="none" stroke="#c8202f" stroke-width="4"/>
  </svg>
  <div class="dots abs"><span></span><span></span><span></span><span></span></div>

  <aside class="donate-panel abs">
    <div class="panel-head">
      <p>Call Today to Donate</p>
      <p class="phone">1-800-555-0142</p>
    </div>
    <p class="panel-note">Or Fill out the form<br>below to instantly donate online</p>
    <div class="form">
      <div class="field">First Name</div><div class="field">Last Name</div>
      <div class="field wide">Phone Number</div>
      <div class="field wide">Email Address</div>
      <div class="field select">Choose Year</div><div class="field select">Choose Make</div>
      <div class="field">Vehicle Model</div><div class="field">Zip Code</div>
      <div class="submit">Donate Your Car</div>
    </div>
  </aside>

  <h2 class="h2 abs steps-title">How It Works</h2>

  <div class="step abs" style="left:62px">
    <svg class="pin" width="78" height="92" viewBox="0 0 78 92"><path d="M39 2a37 37 0 0 1 37 37c0 20-18 30-37 51C20 69 2 59 2 39A37 37 0 0 1 39 2z" fill="#1d5fb4"/><circle cx="39" cy="39" r="29" fill="none" stroke="#fff" stroke-width="2"/><rect x="28" y="26" width="20" height="26" rx="2" fill="none" stroke="#fff" stroke-width="2.5"/><path d="M32 38l5 5 12-12" fill="none" stroke="#fff" stroke-width="2.5"/></svg>
    <h3>1. Fill out the simple form</h3>
    <p>Use our online vehicle donation form to submit your information. Sed ut perspiciatis unde omnis</p>
    <span class="more">Read more ➞</span>
  </div>
  <div class="step abs" style="left:386px">
    <svg class="pin" width="78" height="92" viewBox="0 0 78 92"><path d="M39 2a37 37 0 0 1 37 37c0 20-18 30-37 51C20 69 2 59 2 39A37 37 0 0 1 39 2z" fill="#1d5fb4"/><circle cx="39" cy="39" r="29" fill="none" stroke="#fff" stroke-width="2"/><path d="M24 44v-8l5-9h20l5 9v8z" fill="#fff"/><rect x="31" y="30" width="16" height="6" fill="#1d5fb4"/><circle cx="30" cy="40" r="2" fill="#1d5fb4"/><circle cx="48" cy="40" r="2" fill="#1d5fb4"/><rect x="25" y="44" width="5" height="5" fill="#fff"/><rect x="48" y="44" width="5" height="5" fill="#fff"/></svg>
    <h3>2. Schedule your free pick-up</h3>
    <p>We will arrange to pick up your vehicle when it is most convenient for you. Sed ut perspiciatis unde omnis</p>
    <span class="more">Read more ➞</span>
  </div>
  <div class="step abs" style="left:718px">
    <svg class="pin" width="78" height="92" viewBox="0 0 78 92"><path d="M39 2a37 37 0 0 1 37 37c0 20-18 30-37 51C20 69 2 59 2 39A37 37 0 0 1 39 2z" fill="#1d5fb4"/><circle cx="39" cy="39" r="29" fill="none" stroke="#fff" stroke-width="2"/><rect x="25" y="29" width="28" height="20" rx="2" fill="none" stroke="#fff" stroke-width="2.5"/><path d="M26 31l13 10 13-10" fill="none" stroke="#fff" stroke-width="2.5"/></svg>
    <h3>3. Receive tax deduction</h3>
    <p>Once the vehicle donation is complete, you will receive your tax deductible vehicle donation receipt.</p>
    <span class="more">Read more ➞</span>
  </div>

  <h2 class="h2 abs welcome-title">Welcome To Wheels for Servicemen</h2>
  <p class="welcome-text abs">Every vehicle you give helps a veteran get back on the road to a steady life. Our team handles the paperwork, towing and sale, and the proceeds support programs for disabled servicemen and their families across the country. Giving is simple, free and fully tax deductible, and you can start today in just a few minutes online.</p>
  <div class="donate-btn abs"><i>$</i>DONATE NOW</div>

  <section class="why abs">
    <h2>WHY DONATE YOUR CAR TO US?</h2>
    <ul>
      <li>IRS 501(c)3 Approved: Free 24/7 Pickup with No DMV Hassles.</li>
      <li>Free Local Towing to You: We will pick up your car donation, running or not, when it's most convenient, at home or work.</li>
      <li>All Cars Accepted: We take your car regardless of its condition or registration status.</li>
      <li>Income Tax Deduction: We issue you an IRS tax receipt &amp; offer the largest resale network to get you the highest tax write-off possible.</li>
      <li>No Paperwork Hassles: We take any car and handle everything: DMV, Smog and IRS paperwork.</li>
      <li>Car donations help fund programs: And benefit Allied Veterans Support Fund. An IRS 501(c)3 nonprofit organization.</li>
      <li>Schedule a Free Pickup: Complete the form and a representative will call you to arrange a convenient time to pickup your car.</li>
    </ul>
  </section>
  <div class="why-photo abs" role="img" aria-label="Photo of a uniformed veteran seated in a wheelchair in front of a flag"></div>

  <h2 class="h2 abs tax-title">Tax Deduction Information For Your Car Donation</h2>
  <p class="tax-sub abs">The IRS has set the rules for the tax deduction of your vehicle donation</p>
  <div class="tax-card abs" style="left:100px">
    <h3>If Your Car Donation Sells</h3>
    <h4>for $500 Or Less</h4>
    <p>You can claim the fair market value of your vehicle up to and including $500, or the amount it is sold for if less than fair market value. When you donate your car, you will receive a tax deductible receipt to be submitted with your taxes.</p>
  </div>
  <div class="tax-card abs" style="left:546px">
    <h3>If Your Car Donation Sells</h3>
    <h4>for $501 Or More</h4>
    <p>You can claim the exact amount for which the vehicle is sold. When you donate your car, we will provide you with a tax deductible receipt within 30 days from the sale of your vehicle we will provide you with a 1098-C form to submit with your taxes</p>
  </div>

  <h2 class="h2 abs today-title">Donate Your Car Today!</h2>
  <ul class="checks abs" style="left:266px">
    <li><svg width="12" height="10" viewBox="0 0 12 10"><path d="M1 5l3.5 3.5L11 1" fill="none" stroke="#333" stroke-width="2"/></svg>You have no costs.</li>
    <li><svg width="12" height="10" viewBox="0 0 12 10"><path d="M1 5l3.5 3.5L11 1" fill="none" stroke="#333" stroke-width="2"/></svg>Free towing, running or not.</li>
    <li><svg width="12" height="10" viewBox="0 0 12 10"><path d="M1 5l3.5 3.5L11 1" fill="none" stroke="#333" stroke-width="2"/></svg>We issue you an IRS tax receipt.</li>
  </ul>
  <ul class="checks abs" style="left:546px">
    <li><svg width="12" height="10" viewBox="0 0 12 10"><path d="M1 5l3.5 3.5L11 1" fill="none" stroke="#333" stroke-width="2"/></svg>We take care of all paperwork.</li>
    <li><svg width="12" height="10" viewBox="0 0 12 10"><path d="M1 5l3.5 3.5L11 1" fill="none" stroke="#333" stroke-width="2"/></svg>And we take care of DMV &amp; Smog issues.</li>
  </ul>

  <section class="program abs">
    <h2 class="h2 abs program-title">Car Donation Program</h2>
    <div class="prog-item abs" style="left:172px;top:150px">
      <div class="prog-icon"><svg width="24" height="22" viewBox="0 0 24 22"><path d="M12 21S1 13 1 7a5.5 5.5 0 0 1 11-1 5.5 5.5 0 0 1 11 1c0 6-11 14-11 14z" fill="#fff"/></svg></div>
      <div><h3>Donation Accepted nationwide</h3><p>Lorem ipsum dolor sit amet, consectetur adipiscing elit, sed do eiusmod tempor incididunt</p></div>
    </div>
    <div class="prog-item abs" style="left:596px;top:150px">
      <div class="prog-icon"><svg width="22" height="24" viewBox="0 0 22 24"><rect x="2" y="2" width="16" height="20" fill="none" stroke="#fff" stroke-width="2"/><path d="M6 8h8M6 12h8M6 16h5" stroke="#fff" stroke-width="2"/></svg></div>
      <div><h3>Tax deductible</h3><p>Lorem ipsum dolor sit amet, consectetur adipiscing elit, sed do eiusmod tempor incididunt</p></div>
    </div>
    <div class="prog-item abs" style="left:172px;top:256px">
      <div class="prog-icon"><svg width="26" height="20" viewBox="0 0 26 20"><path d="M2 15v-6l4-7h14l4 7v6z" fill="#fff"/><rect x="3" y="15" width="5" height="4" fill="#fff"/><rect x="18" y="15" width="5" height="4" fill="#fff"/></svg></div>
      <div><h3>All Vehicle</h3><p>Lorem ipsum dolor sit amet, consectetur adipiscing elit, sed do eiusmod tempor incididunt</p></div>
    </div>
    <div class="prog-item abs" style="left:596px;top:256px">
      <div class="prog-icon"><svg width="30" height="20" viewBox="0 0 30 20"><path d="M2 14V8h8l3-5h6v11z" fill="#fff"/><path d="M19 10l9-7" stroke="#fff" stroke-width="2"/><circle cx="7" cy="16" r="3" fill="#fff"/><circle cx="17" cy="16" r="3" fill="#fff"/></svg></div>
      <div><h3>Towing is free</h3><p>Lorem ipsum dolor sit amet, consectetur adipiscing elit, sed do eiusmod tempor incididunt</p></div>
    </div>
  </section>

  <footer class="footer abs">
    <h4 class="abs" style="left:62px;top:44px">Sign up for newsletter</h4>
    <div class="input abs" style="left:62px;top:92px">Enter name</div>
    <div class="input abs" style="left:62px;top:142px">Enter email</div>
    <div class="sub-btn abs" style="left:62px;top:192px">SUBMIT</div>

    <h4 class="abs" style="left:364px;top:40px">Contact Us</h4>
    <ul class="contact abs" style="left:364px;top:80px">
      <li><svg width="10" height="14" viewBox="0 0 10 14"><path d="M5 13S1 8 1 5a4 4 0 0 1 8 0c0 3-4 8-4 8z" fill="#555"/><circle cx="5" cy="5" r="1.5" fill="#f3f3f3"/></svg><span>Wheels for Servicemen<br>418 Harbor Ridge Pkwy. Linden, Nc,<br>27390</span></li>
      <li><svg width="10" height="12" viewBox="0 0 10 12"><path d="M2 1h2l1 3-1.5 1a6 6 0 0 0 3 3L8 7l2 1v2c-5 1-10-4-8-9z" fill="#555"/></svg><span>Phone: 1-800-555-0142</span></li>
      <li><svg width="12" height="10" viewBox="0 0 12 10"><rect x="0.5" y="1" width="11" height="8" fill="#555"/><path d="M1 1.5l5 4 5-4" fill="none" stroke="#f3f3f3"/></svg><span>Email: info@wheelsforservicemen.org</span></li>
    </ul>

    <h4 class="abs" style="left:632px;top:40px">Quick Links</h4>
    <ul class="links abs" style="left:636px;top:78px">
      <li>Home</li><li>About Us</li><li>How It Works</li><li>Charities</li><li>Tax Deduction</li><li>FAQ</li>
    </ul>

    <div class="foot-brand abs" style="left:798px;top:40px"><span class="brand-mark"></span>Wheels for Servicemen</div>
    <div class="badge abs" style="left:830px;top:100px"></div>
    <div class="badge-round abs" style="left:936px;top:98px"></div>
  </footer>

  <div class="bottom abs">
    <div class="socials abs"><span></span><span></span><span></span><span></span></div>
    <p class="copy abs">©2015 - 2016 wheels for servicemen. All Rights Reserved.</p>
  </div>

</div>
</body>
</html>
```